Firm-Asset: Tomorrow - EU-funded management consulting

A website to inform possible customers about my management consulting services for small and medium sized companies. I am using a funding for small and medium companies to do 10 days of workshops and coaching about leadership, further education and employee's health. The Funding is called "Betriebsgut Zukunft" which means something like: Humans are the value of the company. The official logo is attached as a

Target Market(s)

Small and medium sized companies that want to improve their employee's well being and efficiency.

Industry/Entity Type

Management Consulting

Contact Information for Business Card

Malte Quast, Birkenhainweg 14, 10219 Berlin

Logo Text

BetriebsGut Zukunft - Beratung

Font styles to use
Serif
Sans Serif

Requirements
Must have
• a friendly and professional design
Nice to have
• saying somthing about: employees, leadership, further education and employees health are important to us.
Should not have
• should not be too shimmering

```html
<!DOCTYPE html>
<html lang="en">
<head>
<meta charset="utf-8">
<title>BetriebsGut Zukunft – Beratung</title>
<link href="https://fonts.googleapis.com/css2?family=Playfair+Display:wght@400;700&family=Open+Sans:wght@400;600;700&display=swap" rel="stylesheet">
<style>
:root{
  --navy:#173659;
  --navy-dark:#0f2440;
  --sky:#4d86b8;
  --sky-light:#a9cbe6;
  --orange:#e3891c;
  --brown:#a56a2b;
  --grey-bg:#ececec;
  --text:#555;
  --head:#2b2b2b;
  --footer:#1e1e1e;
  --white:#fff;
}
*{margin:0;padding:0;box-sizing:border-box}
html,body{width:727px;height:1200px;overflow:hidden;background:var(--white)}
body{font-family:"Open Sans",Arial,sans-serif;color:var(--text);font-size:8px;position:relative}
.serif{font-family:"Playfair Display",Georgia,serif}

/* header */
.site-header{position:absolute;top:0;left:0;width:727px;height:73px}
.brand{position:absolute;left:30px;top:14px;display:flex;align-items:center;gap:7px}
.brand-mark{width:22px;height:22px;background:var(--orange)}
.brand-name{font-family:"Playfair Display",Georgia,serif;font-weight:700;font-size:15px;color:var(--navy);line-height:1.1}
.brand-tag{position:absolute;left:30px;top:46px;background:var(--navy);color:var(--white);font-size:6px;letter-spacing:1px;padding:2px 8px}
.contact{position:absolute;top:24px;display:flex;align-items:flex-start;gap:6px;font-size:7px;color:#444;line-height:1.5}
.contact svg{flex:none}
.contact.address{left:355px}
.contact.phone{left:560px}

/* nav */
.main-nav{position:absolute;top:73px;left:26px;width:676px;height:24px;background:var(--navy);display:flex;justify-content:space-around;align-items:center}
.main-nav a{color:var(--white);text-decoration:none;font-size:7px;font-weight:600;letter-spacing:.5px}

/* hero */
.hero{position:absolute;top:97px;left:0;width:727px;height:266px}
.hero-photo{position:absolute;inset:0;background:linear-gradient(180deg,#cfe2f1 0%,var(--sky-light) 35%,var(--sky) 80%,#2f5f8e 100%)}
.hero-copy{position:absolute;left:180px;top:62px}
.hero-title{font-family:"Playfair Display",Georgia,serif;font-size:22px;color:var(--navy);letter-spacing:.5px}
.hero-sub{font-family:"Playfair Display",Georgia,serif;font-size:19px;color:var(--orange);line-height:1.2;margin-top:4px}
.btn{display:inline-block;background:var(--brown);color:var(--white);font-size:6.5px;font-weight:600;padding:5px 11px;text-transform:uppercase;letter-spacing:.5px}
.btn.dark{background:var(--navy);margin-top:12px}
.arrow{position:absolute;top:120px;width:18px;height:24px}
.arrow.left{left:18px}.arrow.right{right:18px}

/* about */
.about{position:absolute;top:387px;left:0;width:727px;height:230px}
.about-photo{position:absolute;left:58px;top:12px;width:186px;height:150px;background:linear-gradient(180deg,#d9e4ee,#8ea7bf);border:4px solid var(--white);box-shadow:0 0 0 1px #ddd}
.about-text{position:absolute;left:272px;top:14px;width:420px}
.about-title{font-family:"Playfair Display",Georgia,serif;font-size:12px;color:var(--head);padding-bottom:6px;border-bottom:1px solid #ddd}
.about-title span{color:var(--orange)}
.about-text p{margin-top:8px;line-height:1.6}
.ticks{list-style:none;margin:8px 0 12px}
.ticks li{display:flex;align-items:center;gap:5px;line-height:2}
.ticks li::before{content:"";width:4px;height:4px;border-radius:50%;background:var(--orange)}

/* services */
.services{position:absolute;top:634px;left:0;width:727px;height:281px;background:var(--grey-bg);text-align:center}
.section-title{font-family:"Playfair Display",Georgia,serif;font-size:12px;color:var(--navy);font-weight:700;letter-spacing:.5px}
.services .section-title{margin-top:22px}
.services .lead{font-family:"Playfair Display",Georgia,serif;font-size:7.5px;color:#444;margin-top:14px;letter-spacing:.3px}
.service-list{display:flex;justify-content:space-between;width:590px;margin:26px auto 0}
.service{width:170px}
.service-icon{width:22px;height:22px;border-radius:50%;background:var(--orange);margin:0 auto}
.service h3{font-family:"Playfair Display",Georgia,serif;font-weight:400;font-size:7.5px;color:var(--brown);margin-top:8px;letter-spacing:.3px}
.service p{margin-top:10px;line-height:1.6;font-size:6.5px}
.service .btn{margin-top:12px;background:var(--white);color:#444;border:1px solid #ccc}

/* gallery */
.gallery{position:absolute;top:939px;left:0;width:727px;height:140px}
.gallery .section-title{position:absolute;left:58px;top:6px}
.gallery-nav{position:absolute;right:58px;top:6px;display:flex;gap:3px}
.gallery-nav span{width:12px;height:12px;background:var(--navy)}
.gallery-nav span:last-child{background:#888}
.gallery-rule{position:absolute;left:58px;right:58px;top:26px;border-top:1px solid #ddd}
.gallery-grid{position:absolute;left:58px;top:40px;display:flex;gap:10px}
.gallery-item{width:145px;height:92px;border:3px solid var(--white);box-shadow:0 0 0 1px #ddd}
.g1{background:linear-gradient(180deg,#c9b69a,#7f6a55)}
.g2{background:linear-gradient(180deg,#b9c8d5,#5b738a)}
.g3{background:linear-gradient(180deg,#d8d2c6,#8a7e70)}
.g4{background:linear-gradient(180deg,#d4dde6,#8c9aa8)}

/* footer */
.site-footer{position:absolute;top:1094px;left:0;width:727px;height:106px;background:var(--footer);color:#aaa;text-align:center}
.social{display:flex;justify-content:center;gap:6px;margin-top:14px}
.social span{width:14px;height:14px;background:#4f6fa8}
.social span:nth-child(2){background:#4aa3d8}
.social span:nth-child(3){background:#777}
.social span:nth-child(4){background:#c9442f}
.footer-nav{display:flex;justify-content:center;gap:44px;margin-top:16px;border-top:1px solid #333;border-bottom:1px solid #333;padding:8px 0;width:640px;margin-left:auto;margin-right:auto}
.footer-nav a{color:#ccc;text-decoration:none;font-size:6.5px;letter-spacing:.5px}
.copyright{font-size:6px;margin-top:10px}
</style>
</head>
<body>

<header class="site-header">
  <div class="brand">
    <span class="brand-mark"></span>
    <span class="brand-name">BetriebsGut<br>Zukunft</span>
  </div>
  <div class="brand-tag">BERATUNG · BETRIEBSGUT ZUKUNFT</div>

  <div class="contact address">
    <svg width="9" height="12" viewBox="0 0 9 12"><path d="M4.5 0C2 0 0 2 0 4.5 0 8 4.5 12 4.5 12S9 8 9 4.5C9 2 7 0 4.5 0z" fill="#173659"/><circle cx="4.5" cy="4.5" r="1.6" fill="#fff"/></svg>
    <div>Malte Quast, Birkenhainweg 14<br>10219 Berlin, Germany</div>
  </div>
  <div class="contact phone">
    <svg width="10" height="10" viewBox="0 0 10 10"><path d="M2 0l2 2.5-1 1.2c.6 1.3 1.6 2.3 2.9 2.9L7 5.5 9.5 7.5 8.5 9.5C4 9.5 .5 6 .5 1.5z" fill="#173659"/></svg>
    <div>PH: +49 30 5501 2290<br>E: info@betriebsgut-zukunft.example</div>
  </div>
</header>

<nav class="main-nav">
  <a>HOME</a><a>ABOUT US</a><a>OUR SERVICE</a><a>BLOG</a><a>GALLERY</a><a>CONTACT US</a>
</nav>

<section class="hero">
  <div class="hero-photo" role="img" aria-label="Businessman stepping up a staircase against a city skyline sketch"></div>
  <div class="hero-copy">
    <h1 class="hero-title">BETRIEBSGUT - ZUKUNFT</h1>
    <p class="hero-sub">Services To Small And Medium<br>Sized Companies</p>
    <span class="btn dark">For More About</span>
  </div>
  <svg class="arrow left" viewBox="0 0 18 24"><path d="M12 4L5 12l7 8" stroke="#fff" stroke-width="3" fill="none"/></svg>
  <svg class="arrow right" viewBox="0 0 18 24"><path d="M6 4l7 8-7 8" stroke="#fff" stroke-width="3" fill="none"/></svg>
</section>

<section class="about">
  <div class="about-photo" role="img" aria-label="Business team meeting in an office"></div>
  <div class="about-text">
    <h2 class="about-title">ABOUT : <span>BETRIEBSGUT ZUKUNFT</span></h2>
    <p>Our consulting supports small and medium sized companies with practical workshops and coaching. We help teams grow stronger leaders, healthier staff and steady learning, funded by a public programme for regional businesses across the whole country.</p>
    <ul class="ticks">
      <li>Ten days of workshops and coaching on site</li>
      <li>Funding covers most of the consulting costs</li>
    </ul>
    <span class="btn">More About Us</span>
  </div>
</section>

<section class="services">
  <h2 class="section-title">OUR SERVICES</h2>
  <p class="lead">WE OFFER SERVICES TO SMALL AND MEDIUM SIZED COMPANIES AND CONDUCT THE FOLLOWING PROCESS</p>
  <div class="service-list">
    <article class="service">
      <div class="service-icon"></div>
      <h3>WORKSHOPS ON LEADERSHIP</h3>
      <p>Clear goals, open talks and trust help leaders guide their teams through change every single day.</p>
      <span class="btn">Read More</span>
    </article>
    <article class="service">
      <div class="service-icon"></div>
      <h3>EMPLOYEES HEALTH</h3>
      <p>Healthy staff work with energy. We look at stress, workload and habits to keep people well.</p>
      <span class="btn">Read More</span>
    </article>
    <article class="service">
      <div class="service-icon"></div>
      <h3>FURTHER EDUCATION</h3>
      <p>Learning never stops. We plan training paths that build skills and keep your team ready for tomorrow.</p>
      <span class="btn">Read More</span>
    </article>
  </div>
</section>

<section class="gallery">
  <h2 class="section-title">OUR GALLERY</h2>
  <div class="gallery-nav"><span></span><span></span></div>
  <div class="gallery-rule"></div>
  <div class="gallery-grid">
    <div class="gallery-item g1" role="img" aria-label="Workshop group seated at a table"></div>
    <div class="gallery-item g2" role="img" aria-label="Team discussion in a meeting room"></div>
    <div class="gallery-item g3" role="img" aria-label="Colleagues working together at a desk"></div>
    <div class="gallery-item g4" role="img" aria-label="Presentation to a seated audience"></div>
  </div>
</section>

<footer class="site-footer">
  <div class="social"><span></span><span></span><span></span><span></span></div>
  <nav class="footer-nav">
    <a>HOME</a><a>ABOUT US</a><a>OUR SERVICE</a><a>BLOG</a><a>GALLERY</a><a>CONTACT US</a>
  </nav>
  <p class="copyright">All Rights Reserved. copyright@BetriebsGut Zukunft 2014</p>
</footer>

</body>
</html>
```